Menu Needed for Chicken Wing Concept

We are looking for a print menu for a local wing restaurant called Pluto Hut. This restaurant serves chicken wings and tenders, soft drinks, boozy drinks, dips and fries. The company colors are red and black with slate grey and should be incorporated into the design. I have included renders to show you what the restaurant looks like, source files for the logo (we prefer the "Pluto Hut" logo over the "Pluto Hut Chicken Wings" logo), and a menu in text format. Please let me know if you need any further direction. We prefer trifold menu, standard paper size 8.5 x 11". The client has just given us an example of what they like. You can see the images here:
https://www.fileharbor-example.net/sh/plkmtrwbzeacv7/XQRbTnMvLpKsWdFyHcGjZtEoU?dl=0 Thanks!

Target Market(s)

Americans of all ages and ethnicities

Industry/Entity Type

Restaurant

Requirements
Must have
• Logo colors, all info included

```html
<!DOCTYPE html>
<html lang="en">
<head>
<meta charset="utf-8">
<title>Pluto Hut — Trifold Menu</title>
<link rel="stylesheet" href="https://fonts.googleapis.com/css2?family=Bangers&family=Inter+Tight:ital,wght@0,400;0,600;0,700;1,700&display=swap">
<style>
  :root {
    --red: #e3202f;
    --black: #000000;
    --white: #ffffff;
    --slate: #2f3a45;
    --ink: #111111;
  }
  * { box-sizing: border-box; margin: 0; padding: 0; }
  html, body { width: 1200px; height: 927px; overflow: hidden; background: var(--white); }
  body { font-family: "Inter Tight", Arial, sans-serif; letter-spacing: -0.03em; }
  .menu { position: relative; width: 1200px; height: 927px; overflow: hidden; }
  .panel { position: absolute; top: 0; width: 400px; height: 927px; }
  .panel--left { left: 0; }
  .panel--mid { left: 400px; }
  .panel--right { left: 800px; }

  .band { position: absolute; left: 0; right: 0; }
  .band--black { background: var(--black); color: var(--white); }
  .band--red { background: var(--red); color: var(--white); }
  .band--white { background: var(--white); color: var(--ink); }

  .title, .subtitle {
    position: absolute; left: 0; right: 0; text-align: center;
    font-family: "Bangers", Impact, sans-serif; letter-spacing: 0.06em;
  }
  .title { font-size: 38px; letter-spacing: 0.32em; }
  .subtitle { font-size: 29px; }
  .red-text { color: var(--red); }

  .row { position: absolute; left: 0; right: 0; height: 26px; line-height: 26px; font-size: 19px; }
  .row b { font-weight: 700; }
  .sub { font-weight: 400; }
  .label { position: absolute; left: 22px; }
  .price { position: absolute; width: 80px; text-align: center; margin-left: -40px; }
  .c1 { left: 168px; } .c2 { left: 258px; } .c3 { left: 340px; }
  .head { font-weight: 700; }
  .desc { position: absolute; font-weight: 400; }
  .amount { position: absolute; text-align: right; }

  .highlight { position: absolute; border: 3px solid var(--red); }

  .note { position: absolute; left: 0; right: 0; text-align: center; font-weight: 700; font-style: italic; color: var(--red); font-size: 20px; }
  .intro { position: absolute; left: 20px; top: 72px; font-weight: 700; font-style: italic; font-size: 20px; line-height: 22px; }

  .photo { position: absolute; left: 0; right: 0; }
  .photo--wings { top: 575px; height: 352px; background: radial-gradient(ellipse at 45% 60%, #c06a2e 0%, #8a4420 35%, #3d4a52 70%, #2c3a42 100%); }
  .photo--tenders { top: 383px; height: 121px; background: radial-gradient(ellipse at 55% 50%, #c47a2c 0%, #9b5a22 40%, #4a3a2c 100%); }

  .flavour-box { position: absolute; left: 21px; top: 21px; width: 358px; height: 361px; border: 3px solid var(--white); }
  .list { position: absolute; left: 12px; right: 6px; font-size: 18.5px; line-height: 22.5px; color: var(--white); }
  .list .sep { color: var(--red); padding: 0 4px; }

  .brand { position: absolute; left: 0; right: 0; top: 873px; text-align: center; font-family: "Inter Tight", Arial, sans-serif; font-weight: 700; font-size: 38px; line-height: 52px; color: var(--white); letter-spacing: 0.02em; }
</style>
</head>
<body>
<div class="menu">

  <!-- LEFT PANEL: COMBOS -->
  <section class="panel panel--left">
    <div class="band band--black" style="top:0;height:65px;"><h1 class="title" style="top:12px;">COMBOS</h1></div>
    <div class="band band--red" style="top:65px;height:59px;">
      <p class="intro" style="top:7px;">All Combos come with Fries, Dips,<br>Veggies, and 20oz Fountain Drink.</p>
    </div>
    <div class="band band--white" style="top:124px;height:43px;"><h2 class="subtitle red-text" style="top:7px;">WANGS</h2></div>
    <div class="band band--black" style="top:167px;height:242px;">
      <div class="row head" style="top:19px;"><span class="price c1" style="width:90px;margin-left:-45px;">Boneless</span><span class="price c2">50/50</span><span class="price c3">Bone in</span></div>
      <div class="row" style="top:48px;"><b class="label">6 pieces</b><span class="price c1">$9.19</span><span class="price c2">$10.29</span><span class="price c3">$10.29</span></div>
      <div class="row sub" style="top:76px;"><span class="label">(1 flavour)</span></div>
      <div class="row" style="top:103px;"><b class="label">8 pieces</b><span class="price c1">$11.19</span><span class="price c2">$12.09</span><span class="price c3">$12.29</span></div>
      <div class="row sub" style="top:130px;"><span class="label">(2 flavours)</span></div>
      <div class="highlight" style="left:10px;right:14px;top:164px;height:62px;"></div>
      <div class="row" style="top:167px;"><b class="label">10 pieces</b><span class="price c1" style="top:12px;">$12.99</span><span class="price c2" style="top:12px;">$13.99</span><span class="price c3" style="top:12px;">$14.19</span></div>
      <div class="row sub" style="top:194px;"><span class="label">(2 flavours)</span></div>
    </div>
    <div class="band band--red" style="top:409px;height:42px;"><h2 class="subtitle" style="top:6px;">TENDERS</h2></div>
    <div class="band band--white" style="top:451px;height:124px;">
      <div class="row" style="top:11px;"><b class="label" style="left:24px;">3 pieces</b><span class="desc" style="left:106px;">(1 flavour &amp; 1 dip)</span><span class="amount" style="right:32px;">$8.79</span></div>
      <div class="row" style="top:39px;"><b class="label" style="left:24px;">5 pieces</b><span class="desc" style="left:106px;">(1 flavour &amp; 1 dip)</span><span class="amount" style="right:32px;">$10.69</span></div>
      <div class="highlight" style="left:10px;right:14px;top:74px;height:36px;"></div>
      <div class="row" style="top:78px;"><b class="label" style="left:24px;">8 pieces</b><span class="desc" style="left:106px;">(2 flavours &amp; 2 dips)</span><span class="amount" style="right:32px;">$19.49</span></div>
    </div>
    <div class="photo photo--wings" role="img" aria-label="Photo of glazed sesame chicken wings on a plate with cherry tomatoes and basil"></div>
  </section>

  <!-- MIDDLE PANEL: WANGS & TENDERS BY THE PIECE -->
  <section class="panel panel--mid">
    <div class="band band--black" style="top:0;height:65px;"><h1 class="title" style="top:10px;">WANGS</h1></div>
    <div class="band band--red" style="top:65px;height:41px;"><h2 class="subtitle" style="top:5px;">BY THE PIECE</h2></div>
    <div class="band band--white" style="top:106px;height:450px;">
      <div class="row head" style="top:13px;"><span class="price c1" style="width:90px;margin-left:-45px;">Boneless</span><span class="price c2">50/50</span><span class="price c3" style="width:100px;margin-left:-50px;">Traditional</span></div>
      <div class="row" style="top:46px;"><b class="label">10 pieces</b><span class="price c1">$9.19</span><span class="price c2">$10.29</span><span class="price c3">$10.29</span></div>
      <div class="row sub" style="top:73px;"><span class="label">(2 flavours)</span></div>
      <div class="row" style="top:100px;"><b class="label">15 pieces</b><span class="price c1">$11.19</span><span class="price c2">$12.09</span><span class="price c3">$12.29</span></div>
      <div class="row sub" style="top:127px;"><span class="label">(2 flavours)</span></div>
      <div class="row" style="top:156px;"><b class="label">20 pieces</b><span class="price c1">$9.19</span><span class="price c2">$10.29</span><span class="price c3">$10.29</span></div>
      <div class="row sub" style="top:183px;"><span class="label">(3 flavours)</span></div>
      <div class="row" style="top:211px;"><b class="label">30 pieces</b><span class="price c1">$11.19</span><span class="price c2">$12.09</span><span class="price c3">$12.29</span></div>
      <div class="row sub" style="top:238px;"><span class="label">(4 flavours)</span></div>
      <div class="row" style="top:268px;"><b class="label">50 pieces</b><span class="price c1">$9.19</span><span class="price c2">$10.29</span><span class="price c3">$10.29</span></div>
      <div class="row sub" style="top:295px;"><span class="label">(5 flavours)</span></div>
      <div class="highlight" style="left:10px;right:15px;top:332px;height:62px;"></div>
      <div class="row" style="top:335px;"><b class="label">100 pieces</b><span class="price c1" style="top:4px;">$12.99</span><span class="price c2" style="top:4px;">$13.99</span><span class="price c3" style="top:4px;">$14.19</span></div>
      <div class="row sub" style="top:362px;"><span class="label">(6 flavours)</span></div>
      <p class="note" style="top:411px;text-align:left;left:23px;">Dips Sold Separately.</p>
    </div>
    <div class="band band--black" style="top:556px;height:61px;"><h1 class="title" style="top:10px;">TENDERS</h1></div>
    <div class="band band--white" style="top:617px;height:41px;"><h2 class="subtitle red-text" style="top:5px;">BY THE PIECE</h2></div>
    <div class="band band--black" style="top:658px;height:213px;">
      <div class="row" style="top:13px;"><b class="label" style="left:20px;">4 pieces</b><span class="desc" style="left:103px;">(1 flavour &amp; 1 dip)</span><span class="amount" style="right:36px;">$8.79</span></div>
      <div class="row" style="top:41px;"><b class="label" style="left:20px;">7 pieces</b><span class="desc" style="left:101px;">(2 flavours &amp; 2 dips)</span><span class="amount" style="right:36px;">$10.69</span></div>
      <div class="row" style="top:68px;"><b class="label" style="left:20px;">15 pieces</b><span class="desc" style="left:110px;">(3 flavours &amp; 3 dips)</span><span class="amount" style="right:36px;">$8.79</span></div>
      <div class="row" style="top:96px;"><b class="label" style="left:20px;">20 pieces</b><span class="desc" style="left:115px;">(4 flavours &amp; 4 dips)</span><span class="amount" style="right:36px;">$10.69</span></div>
      <div class="highlight" style="left:6px;right:19px;top:125px;height:37px;"></div>
      <div class="row" style="top:130px;"><b class="label" style="left:20px;">30 pieces</b><span class="desc" style="left:115px;">(5 flavours &amp; 5 dips)</span><span class="amount" style="right:36px;">$19.49</span></div>
      <p class="note" style="top:175px;">All Fries, Veggies, and Dips Sold Separately.</p>
    </div>
    <div class="band band--red" style="top:871px;height:56px;"></div>
    <div class="brand">Pluto Hut</div>
  </section>

  <!-- RIGHT PANEL: FLAVOURS & SIDES -->
  <section class="panel panel--right">
    <div class="band band--black" style="top:0;height:383px;">
      <div class="flavour-box">
        <h2 class="subtitle red-text" style="top:9px;font-size:30px;">WANG FLAVOURS</h2>
        <p class="list" style="top:46px;">The Pluto Reaper<span class="sep">|</span>Teriyaki<span class="sep">|</span>Texas BBQ<br>Mild<span class="sep">|</span>New Orleans Spicy<span class="sep">|</span>Traditional Hot<br>Spicy Korean BBQ<span class="sep">|</span>Bangin Jamaican Jerk<br>Mango Haberero<span class="sep">|</span>Honey BBQ<span class="sep">|</span>Gojugang<br>Pineapple Bang<span class="sep">|</span>Lemon Pepper<span class="sep">|</span>Spicy<br>Garlic<span class="sep">|</span>Garlic Parmesan</p>
        <h2 class="subtitle red-text" style="top:188px;font-size:30px;">DRY RUBS</h2>
        <p class="list" style="top:220px;">Lemon Pepper<span class="sep">|</span>New Orleans Spicy<br>Garlic Parmesan</p>
        <h2 class="subtitle red-text" style="top:268px;font-size:30px;">DIPS</h2>
        <p class="list" style="top:302px;">Ranch<span class="sep">|</span>Spicy Ranch<span class="sep">|</span>Honey Mustard<br>Bleu Cheese<span class="sep">|</span>Cheese Sauce</p>
      </div>
    </div>
    <div class="photo photo--tenders" role="img" aria-label="Photo of crispy chicken tenders with fries in a bowl"></div>
    <div class="band band--black" style="top:504px;height:67px;"><h1 class="title" style="top:13px;">SIDES</h1></div>
    <div class="band band--red" style="top:571px;height:42px;"><h2 class="subtitle" style="top:6px;">FRIES</h2></div>
    <div class="band band--white" style="top:613px;height:216px;">
      <div class="row head" style="top:10px;"><span class="price" style="left:259px;">Regular</span><span class="price" style="left:350px;">Large</span></div>
      <div class="row" style="top:38px;"><b class="label" style="left:20px;">Regular Fries</b><span class="price" style="left:259px;">$2.99</span><span class="price" style="left:350px;">$4.99</span></div>
      <div class="row" style="top:67px;"><b class="label" style="left:20px;">Cajun Fries</b><span class="price" style="left:259px;">$2.99</span><span class="price" style="left:350px;">$4.99</span></div>
      <div class="row" style="top:95px;"><b class="label" style="left:20px;">Hut Fries</b><span class="price" style="left:259px;">$2.99</span><span class="price" style="left:350px;">$4.99</span></div>
      <div class="row" style="top:125px;"><b class="label" style="left:20px;">Garlic Parmesan</b><span class="price" style="left:259px;">$3.99</span><span class="price" style="left:350px;">$5.49</span></div>
      <div class="row" style="top:153px;"><b class="label" style="left:20px;">Cheese Fries</b><span class="price" style="left:259px;">$3.99</span><span class="price" style="left:350px;">$5.49</span></div>
      <div class="row" style="top:182px;"><b class="label" style="left:20px;">Chilli Cheese Fries</b><span class="price" style="left:259px;">$4.99</span><span class="price" style="left:350px;">$5.99</span></div>
    </div>
    <div class="band band--red" style="top:829px;height:42px;"><h2 class="subtitle" style="top:6px;">VEGGIES</h2></div>
    <div class="band band--white" style="top:871px;height:56px;">
      <div class="row" style="top:6px;"><b class="label" style="left:21px;">Carrots, celery, or 50/50</b><span class="price" style="left:349px;">$3.99</span></div>
    </div>
  </section>

</div>
</body>
</html>
```